Commercial Real Estate

We need a business card design for a new commercial real estate business that specializes in apartment building brokerage. Not individual units but the entire complex. We find and represent the owners existing buildings and well as new buyers for those buildings. The design should convey trust, integrity, knowledge and growth. It should be easily read.

Target Market(s)

40 to 65 years old

Industry/Entity Type

Real Estate

```html
<!DOCTYPE html>
<html lang="en">
<head>
<meta charset="utf-8">
<title>Brightwell Property Investments – Business Card</title>
<link href="https://fonts.googleapis.com/css2?family=Roboto+Condensed:ital,wght@0,400;0,700;1,700&display=swap" rel="stylesheet">
<style>
  :root {
    --backdrop: #6ccaca;
    --card-dark: #3d4f50;
    --card-mid: #4a5c5d;
    --accent: #6ecdcb;
    --ink-light: #ffffff;
  }
  html, body {
    margin: 0;
    padding: 0;
    width: 1200px;
    height: 900px;
    overflow: hidden;
    background: var(--backdrop);
  }
  .canvas {
    position: relative;
    width: 1200px;
    height: 900px;
    font-family: "Roboto Condensed", sans-serif;
  }
  .card {
    position: absolute;
    left: 372px;
    top: 50px;
    width: 456px;
    height: 800px;
    border-radius: 44px;
    background: linear-gradient(135deg, var(--card-mid) 0%, var(--card-dark) 55%, #3a4b4c 100%);
    overflow: hidden;
    color: var(--ink-light);
  }
  .card-guides {
    position: absolute;
    left: 0;
    top: 0;
  }
  .text-block {
    position: absolute;
    left: 116px;
    margin: 0;
    line-height: 1;
    white-space: nowrap;
  }
  .person-name {
    top: 142px;
    font-size: 38px;
    font-weight: 700;
    color: var(--accent);
    letter-spacing: 0.5px;
  }
  .person-role {
    top: 190px;
    font-size: 21px;
    font-weight: 400;
  }
  .company-name {
    top: 293px;
    font-size: 25px;
    font-weight: 700;
    color: var(--accent);
  }
  .company-address {
    top: 325px;
    font-size: 24px;
    line-height: 31px;
  }
  .contact-line {
    font-size: 24px;
  }
  .contact-phone { top: 442px; }
  .contact-mobile { top: 480px; }
  .contact-email { top: 518px; }
  .contact-web {
    top: 556px;
    font-style: italic;
    font-weight: 700;
  }
  .contact-web .web-domain { color: var(--accent); }
  .brand-name {
    position: absolute;
    left: 178px;
    top: 668px;
    margin: 0;
    font-size: 40px;
    font-weight: 700;
    color: var(--ink-light);
    letter-spacing: 1px;
    line-height: 1;
  }
</style>
</head>
<body>
<main class="canvas">
  <section class="card" aria-label="Business card">
    <svg class="card-guides" width="456" height="800" viewBox="0 0 456 800" aria-hidden="true">
      <g stroke="var(--accent)" stroke-width="2.5" fill="none">
        <line x1="90" y1="0" x2="90" y2="143"/>
        <line x1="90" y1="182" x2="90" y2="293"/>
        <line x1="90" y1="332" x2="90" y2="432"/>
        <line x1="90" y1="590" x2="90" y2="618"/>
        <line x1="90" y1="758" x2="90" y2="800"/>
        <circle class="brand-circle" cx="90" cy="688" r="70"/>
      </g>
      <g fill="var(--accent)">
        <!-- person -->
        <circle cx="90" cy="154" r="7"/>
        <path d="M78 175 q0 -13 12 -13 q12 0 12 13 z"/>
        <!-- pin -->
        <path d="M90 328 c-4 -7 -11 -13 -11 -20 a11 11 0 0 1 22 0 c0 7 -7 13 -11 20 z"/>
        <circle cx="90" cy="308" r="4.5" fill="var(--card-dark)"/>
        <!-- phone -->
        <path d="M78 454 q12 -10 24 0 l-2 4 h-5 l-1 -3 h-8 l-1 3 h-5 z"/>
        <rect x="81" y="458" width="18" height="10" rx="2"/>
        <!-- mobile -->
        <rect x="83" y="486" width="14" height="22" rx="2"/>
        <rect x="86" y="489" width="8" height="12" fill="var(--card-dark)"/>
        <!-- envelope -->
        <rect x="78" y="528" width="24" height="16" rx="1"/>
        <path d="M79 529 l11 9 l11 -9" stroke="var(--card-dark)" stroke-width="1.8" fill="none"/>
      </g>
      <!-- globe -->
      <g stroke="var(--accent)" stroke-width="1.6" fill="none">
        <circle cx="90" cy="572" r="10"/>
        <ellipse cx="90" cy="572" rx="4.5" ry="10"/>
        <line x1="80" y1="572" x2="100" y2="572"/>
        <path d="M82 566 h16 M82 578 h16"/>
      </g>
    </svg>

    <h1 class="text-block person-name">HARLAN REED</h1>
    <p class="text-block person-role">Managing Director</p>

    <p class="text-block company-name">Brightwell Property Investments</p>
    <p class="text-block company-address">Address, Land dummy<br>dummy dummy City</p>

    <p class="text-block contact-line contact-phone">00 0000 0000</p>
    <p class="text-block contact-line contact-mobile">0000 000 000</p>
    <p class="text-block contact-line contact-email">harlan.reed@brightwell-pi.com</p>
    <p class="text-block contact-line contact-web">www.<span class="web-domain">brightwell-pi</span>.com</p>

    <p class="brand-name">Brightwell</p>
  </section>
</main>
</body>
</html>
```